Harborline Renewal Business Card Design

Professional and clean design. The design colors should flow with the logo. Two-sided card with the website on the back which is:

www.HarborlineRenewal.example.

"Specializing in Water Damage Restoration"

On the front I need the name, email, phone, and logo.

Name: Darnell Quisby
Email: Darnell@HarborlineRenewal.example
Phone: 555-318-2046 for now

I only have the Preview and Thumbnail right now but should have the source files uploaded within a day or two.

Target Market(s)

Flood victims, home owners with water damage from busted pipes etc...

Industry/Entity Type

Business

Contact Information for Business Card

Name: Darnell Quisby

Font styles to use
Serif
Sans Serif

Requirements
Must have
• Business Card Details Info

```html
<!DOCTYPE html>
<html lang="en">
<head>
<meta charset="utf-8">
<title>Harborline Renewal – Business Card</title>
<link href="https://fonts.googleapis.com/css2?family=Cinzel:wght@400;600&family=Open+Sans:wght@400;600&display=swap" rel="stylesheet">
<style>
  :root {
    --page-bg: #eceae6;
    --card-white: #ffffff;
    --card-shade: #f1f2f3;
    --blue-text: #2aa8d6;
    --blue-deep: #1c95c6;
    --blue-mid: #2db4db;
    --blue-light: #86d3ec;
    --ink-white: #ffffff;
  }
  * { margin: 0; padding: 0; box-sizing: border-box; }
  html, body {
    width: 1200px; height: 780px; overflow: hidden;
    background: var(--page-bg);
  }
  .stage {
    position: relative; width: 1200px; height: 780px;
    display: flex; align-items: center; justify-content: center; gap: 40px;
  }
  .card {
    position: relative; width: 540px; height: 309px;
    background: linear-gradient(160deg, var(--card-white) 40%, var(--card-shade));
    box-shadow: 0 6px 18px rgba(0,0,0,.18);
    overflow: hidden;
  }
  .card-band { position: absolute; inset: 0; width: 100%; height: 100%; }

  .brand { position: absolute; display: flex; align-items: center; gap: 12px; }
  .brand-dot {
    width: 46px; height: 46px; border-radius: 50%;
    background: var(--blue-mid); flex: none;
  }
  .brand-name {
    font-family: "Cinzel", serif; font-weight: 600;
    color: var(--blue-text); font-size: 23px; letter-spacing: 1px;
    text-transform: uppercase; line-height: 1;
  }
  .tagline {
    position: absolute; font-family: "Open Sans", sans-serif;
    font-size: 11.5px; color: var(--blue-text); letter-spacing: .3px;
  }

  .front .brand { left: 222px; top: 36px; }
  .front .tagline { left: 280px; top: 90px; }

  .holder-name {
    position: absolute; left: 34px; top: 150px;
    font-family: "Cinzel", serif; font-weight: 600; font-size: 18px;
    color: var(--blue-text); letter-spacing: 1px; text-transform: uppercase;
  }
  .contact-list { position: absolute; left: 34px; top: 198px; list-style: none; }
  .contact-item {
    display: flex; align-items: center; gap: 8px; margin-bottom: 6px;
    font-family: "Open Sans", sans-serif; font-size: 12.5px; color: var(--blue-text);
  }
  .contact-icon { width: 15px; height: 15px; flex: none; }

  .website {
    position: absolute; font-family: "Open Sans", sans-serif;
    font-size: 13.5px; color: var(--ink-white); letter-spacing: .3px;
  }
  .front .website { right: 24px; bottom: 24px; }

  .back .brand { left: 50%; top: 92px; transform: translateX(-50%); }
  .back .tagline { left: 0; right: 0; top: 146px; text-align: center; }
  .back .website { left: 24px; bottom: 24px; }
</style>
</head>
<body>
<main class="stage">

  <section class="card front" aria-label="Card front">
    <svg class="card-band" viewBox="0 0 540 309" preserveAspectRatio="none" aria-hidden="true">
      <path d="M0,309 L0,262 C160,258 330,226 420,150 C470,108 510,92 540,86 L540,309 Z" fill="var(--blue-light)"/>
      <path d="M0,309 L0,274 C170,270 340,238 428,164 C474,124 512,106 540,100 L540,309 Z" fill="var(--card-white)"/>
      <path d="M0,309 L0,284 C180,282 350,252 440,180 C484,144 516,124 540,118 L540,309 Z" fill="var(--blue-mid)"/>
      <path d="M140,309 C300,300 430,262 540,200 L540,309 Z" fill="var(--blue-deep)" opacity=".55"/>
    </svg>

    <div class="brand">
      <span class="brand-dot"></span>
      <span class="brand-name">Harborline Renewal</span>
    </div>
    <p class="tagline">Specializing in Water Damage Restoration</p>

    <h1 class="holder-name">Darnell Quisby</h1>
    <ul class="contact-list">
      <li class="contact-item">
        <svg class="contact-icon" viewBox="0 0 16 16" aria-hidden="true">
          <rect width="16" height="16" rx="2" fill="var(--blue-mid)"/>
          <path d="M4.5 3.5h2l1 2.5-1.3 1a6 6 0 0 0 2.8 2.8l1-1.3 2.5 1v2a1 1 0 0 1-1 1A8 8 0 0 1 3.5 4.5a1 1 0 0 1 1-1z" fill="var(--ink-white)"/>
        </svg>
        <span>555-318-2046</span>
      </li>
      <li class="contact-item">
        <svg class="contact-icon" viewBox="0 0 16 16" aria-hidden="true">
          <rect width="16" height="16" rx="2" fill="var(--blue-mid)"/>
          <rect x="3" y="4.5" width="10" height="7" fill="none" stroke="var(--ink-white)" stroke-width="1.2"/>
          <path d="M3 4.5l5 4 5-4" fill="none" stroke="var(--ink-white)" stroke-width="1.2"/>
        </svg>
        <span>Darnell@HarborlineRenewal.example</span>
      </li>
    </ul>

    <p class="website">www.HarborlineRenewal.example</p>
  </section>

  <section class="card back" aria-label="Card back">
    <svg class="card-band" viewBox="0 0 540 309" preserveAspectRatio="none" aria-hidden="true">
      <path d="M540,309 L540,262 C380,258 210,226 120,150 C70,108 30,92 0,86 L0,309 Z" fill="var(--blue-light)"/>
      <path d="M540,309 L540,274 C370,270 200,238 112,164 C66,124 28,106 0,100 L0,309 Z" fill="var(--card-white)"/>
      <path d="M540,309 L540,284 C360,282 190,252 100,180 C56,144 24,124 0,118 L0,309 Z" fill="var(--blue-mid)"/>
      <path d="M400,309 C240,300 110,262 0,200 L0,309 Z" fill="var(--blue-deep)" opacity=".55"/>
    </svg>

    <div class="brand">
      <span class="brand-dot"></span>
      <span class="brand-name">Harborline Renewal</span>
    </div>
    <p class="tagline">Specializing in Water Damage Restoration</p>

    <p class="website">www.HarborlineRenewal.example</p>
  </section>

</main>
</body>
</html>
```